New iOS App design for Boston Startup

We are looking for a new app design for our iPhone app. The current app's design feels outdated and we like to add lots of new functionality and a new navigation as well. A complete overhaul therefore!
We want you to design 5 screens that will have changed the most. The complete wireframes of these 5 pages are attached in the requirements document.
Once the winning design is selected we will award the winner with the designing all other screens (40-50 screens based on the same design). This will be a separate project worth $1000. The winning designer can get more follow up work if both sides are happy about the cooperation.
We will give feedback as soon as the first screen has been uploaded for review. Final decision will be made only after all 5 screens are finished.
We hope you give it your best!
Note: will only communicate through PixelHarbor (no skype),
Updates
Reason: Want to give designers a chance to submit their designs as I understand from some, the deadline is too close.
I have raised the award and introduced a 2nd price as well to make it worth your time. I hope you give it your best shot.
Reason: A few of you have asked for an extension of the deadline as time is running out. I will extend by one day. Tell me if you need more.
Industry/Entity Type
Startup
Requirements
Must have
- At least 1 screen before we can give you feedback.
Nice to have
- multiple options of 1 screen to get to a desirable design

```html
<!DOCTYPE html>
<html lang="en">
<head>
<meta charset="utf-8">
<title>Study App – Side Menu</title>
<link href="https://fonts.googleapis.com/css2?family=Roboto:wght@300;400;500&display=swap" rel="stylesheet">
<style>
  :root {
    --status-bg: #000000;
    --status-text: #ffffff;
    --header-top: #c9d3de;
    --header-bottom: #b7c3d0;
    --header-text: #3a3f46;
    --panel-top: #2f3d4e;
    --panel-bottom: #243140;
    --divider: rgba(210, 216, 224, 0.55);
    --menu-text: #ffffff;
    --accent-red: #ea4f55;
    --badge-green: #3cb84a;
    --badge-blue: #4a9fe4;
    --photo-top: #9fb2c6;
    --photo-bottom: #5f7489;
    --stats-bg: #e4e8ec;
    --stats-text: #1e2226;
    --stats-sub: #4a4f55;
    --content-bg: #ffffff;
    --rule: #dfe2e5;
    --green-circle: #41be53;
    --footer-bg: #f4f5f6;
    --footer-text: #555a60;
  }
  * { margin: 0; padding: 0; box-sizing: border-box; }
  html, body { width: 676px; height: 1200px; overflow: hidden; background: #ffffff; }
  body { font-family: "Roboto", "Helvetica Neue", Arial, sans-serif; }
  .screen { position: relative; width: 676px; height: 1200px; overflow: hidden; background: var(--content-bg); }

  .status-bar {
    position: absolute; left: 0; top: 0; width: 676px; height: 42px;
    background: var(--status-bg); color: var(--status-text);
    font-size: 24px; font-weight: 500;
  }
  .status-bar .carrier { position: absolute; left: 8px; top: 7px; display: flex; align-items: center; gap: 8px; }
  .status-bar .time { position: absolute; left: 0; width: 676px; text-align: center; top: 7px; }
  .status-bar .battery-area { position: absolute; right: 8px; top: 8px; display: flex; gap: 14px; align-items: center; }

  /* Right-hand content peeking behind the menu */
  .content { position: absolute; left: 582px; top: 42px; width: 94px; height: 1158px; }
  .content .topbar { position: absolute; left: 0; top: 0; width: 94px; height: 93px; background: var(--accent-red); }
  .content .hamburger { position: absolute; left: 24px; top: 28px; }
  .content .cover { position: absolute; left: 0; top: 93px; width: 94px; height: 298px; background: linear-gradient(160deg, var(--photo-top), var(--photo-bottom)); }
  .content .avatar { position: absolute; left: 17px; top: 60px; width: 180px; height: 180px; border-radius: 50%; border: 5px solid #ffffff; background: linear-gradient(150deg, #c9a48c, #7d6a60); }
  .content .stats { position: absolute; left: 0; top: 391px; width: 94px; height: 104px; background: var(--stats-bg); }
  .content .stats .value { position: absolute; left: 31px; top: 12px; font-size: 34px; color: var(--stats-text); white-space: nowrap; }
  .content .stats .label { position: absolute; left: 34px; top: 56px; font-size: 30px; font-weight: 300; color: var(--stats-sub); white-space: nowrap; }
  .content .stats-rule { position: absolute; left: 0; top: 495px; width: 94px; height: 4px; background: var(--accent-red); }
  .content .progress-ring { position: absolute; left: 22px; top: 555px; width: 196px; height: 196px; border-radius: 50%; background: var(--green-circle); box-shadow: 0 2px 3px rgba(0,0,0,0.25); }
  .content .progress-ring span { position: absolute; left: 28px; top: 76px; color: #ffffff; font-size: 30px; white-space: nowrap; }
  .content .rule-a { position: absolute; left: 0; top: 783px; width: 94px; height: 3px; background: var(--rule); }
  .content .rule-b { position: absolute; left: 0; top: 1018px; width: 94px; height: 3px; background: var(--rule); }
  .content .tab { position: absolute; left: 0; top: 1021px; width: 94px; height: 137px; background: var(--footer-bg); }
  .content .tab svg { position: absolute; left: 50px; top: 22px; }
  .content .tab span { position: absolute; left: 47px; top: 80px; font-size: 21px; color: var(--footer-text); white-space: nowrap; }

  /* Side menu */
  .menu { position: absolute; left: 0; top: 42px; width: 582px; height: 1158px; }
  .menu-header {
    height: 93px; background: linear-gradient(180deg, var(--header-top), var(--header-bottom));
    display: flex; align-items: center; justify-content: center;
    font-size: 40px; font-weight: 400; color: var(--header-text);
  }
  .menu-list {
    list-style: none; height: 1065px;
    background: linear-gradient(165deg, var(--panel-top) 0%, #3a4a5c 45%, var(--panel-bottom) 100%);
  }
  .menu-item {
    position: relative; height: 122.5px; display: flex; align-items: center;
    border-bottom: 2px solid var(--divider); color: var(--menu-text);
    font-size: 33px; font-weight: 400; line-height: 1.2;
  }
  .menu-item .icon { position: absolute; left: 24px; top: 50%; transform: translateY(-50%); width: 38px; height: 38px; }
  .menu-item .label { padding-left: 91px; padding-right: 60px; }
  .menu-item .badge {
    position: absolute; right: 32px; top: 50%; transform: translateY(-50%);
    width: 41px; height: 41px; border-radius: 3px; color: #ffffff;
    font-size: 25px; display: flex; align-items: center; justify-content: center;
  }
  .badge.green { background: var(--badge-green); }
  .badge.blue { background: var(--badge-blue); }
</style>
</head>
<body>
<div class="screen">

  <div class="status-bar">
    <div class="carrier">
      <svg width="36" height="20" viewBox="0 0 36 20" aria-hidden="true">
        <rect x="0" y="14" width="5" height="6" fill="#fff"/><rect x="7" y="11" width="5" height="9" fill="#fff"/>
        <rect x="14" y="8" width="5" height="12" fill="#fff"/><rect x="21" y="4" width="5" height="16" fill="#fff"/>
        <rect x="28" y="0" width="5" height="20" fill="#fff"/>
      </svg>
      <span>NOVA&nbsp;&nbsp;3G</span>
    </div>
    <div class="time">9:51 PM</div>
    <div class="battery-area">
      <svg width="22" height="22" viewBox="0 0 22 22" aria-hidden="true">
        <circle cx="11" cy="11" r="10" fill="#fff"/><path d="M11 5v6h4" stroke="#000" stroke-width="2" fill="none"/>
      </svg>
      <svg width="48" height="22" viewBox="0 0 48 22" aria-hidden="true">
        <rect x="1" y="1" width="41" height="20" rx="3" fill="none" stroke="#fff" stroke-width="2"/>
        <rect x="4" y="4" width="35" height="14" fill="#fff"/><rect x="43" y="7" width="4" height="8" fill="#fff"/>
      </svg>
    </div>
  </div>

  <div class="content">
    <div class="topbar">
      <svg class="hamburger" width="48" height="38" viewBox="0 0 48 38" aria-label="Open menu">
        <rect x="0" y="0" width="48" height="7" rx="2" fill="#fff"/>
        <rect x="0" y="15" width="48" height="7" rx="2" fill="#fff"/>
        <rect x="0" y="30" width="48" height="7" rx="2" fill="#fff"/>
      </svg>
    </div>
    <div class="cover" role="img" aria-label="Profile cover photo of glass building facade">
      <div class="avatar" role="img" aria-label="Tutor profile portrait"></div>
    </div>
    <div class="stats">
      <div class="value">34%</div>
      <div class="label">Complete</div>
    </div>
    <div class="stats-rule"></div>
    <div class="progress-ring"><span>Analysis</span></div>
    <div class="rule-a"></div>
    <div class="rule-b"></div>
    <div class="tab">
      <svg width="44" height="44" viewBox="0 0 44 44" aria-hidden="true">
        <rect x="2" y="4" width="36" height="8" rx="1" fill="#555a60"/>
        <rect x="6" y="15" width="36" height="8" rx="1" fill="#555a60"/>
        <rect x="0" y="26" width="38" height="8" rx="1" fill="#555a60"/>
        <rect x="4" y="37" width="38" height="7" rx="1" fill="#555a60"/>
      </svg>
      <span>Theory</span>
    </div>
  </div>

  <nav class="menu">
    <div class="menu-header">Menu</div>
    <ul class="menu-list">
      <li class="menu-item">
        <svg class="icon" viewBox="0 0 38 38" aria-hidden="true">
          <rect x="2" y="3" width="32" height="32" rx="2" fill="var(--accent-red)"/>
          <circle cx="18" cy="15" r="6" fill="#2f3d4e"/><path d="M7 33c1-7 6-10 11-10s10 3 11 10z" fill="#2f3d4e"/>
        </svg>
        <span class="label">Profile</span>
      </li>
      <li class="menu-item">
        <svg class="icon" viewBox="0 0 38 38" aria-hidden="true">
          <path d="M36 3L2 17l12 4 3 13 5-9 9 6z" fill="none" stroke="var(--accent-red)" stroke-width="3" stroke-linejoin="round"/>
          <path d="M14 21L36 3" stroke="var(--accent-red)" stroke-width="3"/>
        </svg>
        <span class="label">My Tutor</span>
        <span class="badge green">8</span>
      </li>
      <li class="menu-item">
        <svg class="icon" viewBox="0 0 38 38" aria-hidden="true">
          <path d="M18 6H4v28h28V20" fill="none" stroke="var(--accent-red)" stroke-width="3.5"/>
          <path d="M14 24l2-7L32 2l5 5-15 15z" fill="var(--accent-red)"/>
        </svg>
        <span class="label">Advanced Writing Assignment (AWA)</span>
      </li>
      <li class="menu-item">
        <svg class="icon" viewBox="0 0 38 38" aria-hidden="true">
          <circle cx="24" cy="11" r="6" fill="#d94a50"/><path d="M14 30c1-7 5-10 10-10s9 3 10 10z" fill="#d94a50"/>
          <circle cx="14" cy="13" r="6" fill="var(--accent-red)"/><path d="M2 32c1-7 6-10 12-10s11 3 12 10z" fill="var(--accent-red)"/>
        </svg>
        <span class="label">Social</span>
        <span class="badge blue">6</span>
      </li>
      <li class="menu-item">
        <svg class="icon" viewBox="0 0 38 38" aria-hidden="true">
          <rect x="4" y="2" width="28" height="34" rx="2" fill="var(--accent-red)"/>
          <rect x="18" y="13" width="16" height="12" rx="2" fill="#2f3d4e"/>
          <circle cx="24" cy="19" r="2.5" fill="var(--accent-red)"/>
        </svg>
        <span class="label">Vocabulary</span>
      </li>
      <li class="menu-item">
        <svg class="icon" viewBox="0 0 38 38" aria-hidden="true">
          <path d="M1 6h7l4 18h20l4-13H10" fill="none" stroke="var(--accent-red)" stroke-width="3.5" stroke-linejoin="round"/>
          <path d="M11 12h24l-3 11H13z" fill="var(--accent-red)"/>
          <circle cx="14" cy="31" r="3" fill="var(--accent-red)"/><circle cx="29" cy="31" r="3" fill="var(--accent-red)"/>
        </svg>
        <span class="label">Marketplace</span>
      </li>
      <li class="menu-item">
        <svg class="icon" viewBox="0 0 38 38" aria-hidden="true">
          <g fill="var(--accent-red)">
            <circle cx="19" cy="19" r="11"/>
            <rect x="16" y="2" width="6" height="34" rx="1"/>
            <rect x="16" y="2" width="6" height="34" rx="1" transform="rotate(45 19 19)"/>
            <rect x="16" y="2" width="6" height="34" rx="1" transform="rotate(90 19 19)"/>
            <rect x="16" y="2" width="6" height="34" rx="1" transform="rotate(135 19 19)"/>
          </g>
          <circle cx="19" cy="19" r="5" fill="#2f3d4e"/>
        </svg>
        <span class="label">Settings</span>
      </li>
      <li class="menu-item">
        <svg class="icon" viewBox="0 0 38 38" aria-hidden="true">
          <circle cx="19" cy="19" r="16" fill="var(--accent-red)"/>
          <circle cx="19" cy="11" r="2.5" fill="#2f3d4e"/><rect x="16.5" y="16" width="5" height="13" fill="#2f3d4e"/>
        </svg>
        <span class="label">About the GradeX</span>
      </li>
    </ul>
  </nav>

</div>
</body>
</html>
```